Business Card Design for Retail Product Line

We need a two-sided, full-color business card for a new oral care product line. The feel of the card should invoke emotions of happiness and health. It should be bright, cheerful and modern in appearance. The card should be mostly matte finish, but with elements of spot-gloss and/or raised/embossed features (print, logo, tag lines, etc.).

Target Market(s)

People who are into whole-body health, eat well and understand the importance of nutrition.

Industry/Entity Type

Health And Wellness

Contact Information for Business Card

The logo, color scheme and tag-lines have all been developed and artwork is attached. Card is to be standard-sized and should use a mix of clean, sans-serif fonts; the main font (DIN) is attached as well. The card will be used for 3 individuals and should include placeholders for:
1. Name
2. Title (for example, "CEO")
3. Business address
4. Phone number
5. Website
6. Email address

Font styles to use
Sans Serif
Other font styles liked:
• DIN font

Colors
faa54b
000000
5c5c5c
a2ce44

Requirements
Must have
• 2 sides
• Full color orange on one side
• Image of DNA leaves
• Tag line "Smile from the Inside Out", on single side with orange background
• Company Logo (Plure) on same side as text (name, phone, address, etc.)
• Name, Title, Business Address, Phone Number, Website, Email address
• UPDATE: "Brisk Meadow", not "Brisk M Eadow"
Should not have
• Calligraphy
• Dark colors
• UPDATE!! Do not include "Turmeric infused toothpaste" on the business card
• UPDATE #2!! Do not include "Brisk Meadow" on the business card

```html
<!DOCTYPE html>
<html lang="en">
<head>
<meta charset="utf-8">
<title>Plure — Business Card</title>
<link rel="stylesheet" href="https://fonts.googleapis.com/css2?family=Barlow:wght@400;500;600&display=swap">
<style>
  :root {
    --page-bg: #ece8e1;
    --orange-light: #f2cc3c;
    --orange-mid: #efbe3a;
    --orange-deep: #e69a2f;
    --white: #ffffff;
    --ink: #5c5c5c;
    --green: #8cc63f;
    --leaf-dark: #3fae49;
    --helix-grey: #c9cacc;
  }
  * { box-sizing: border-box; margin: 0; padding: 0; }
  html, body {
    width: 1200px; height: 1076px; overflow: hidden;
    background: var(--page-bg);
  }
  .canvas { position: relative; width: 1200px; height: 1076px; }
  .card {
    position: absolute; left: 220px; width: 760px; height: 437px;
    box-shadow: 0 6px 18px rgba(0,0,0,0.18);
    overflow: hidden;
  }
  /* Front side */
  .card--front {
    top: 60px;
    background: linear-gradient(160deg, var(--orange-deep) 0%, var(--orange-light) 38%, var(--orange-mid) 62%, var(--orange-deep) 100%);
  }
  .brand-name {
    position: absolute; left: 0; right: 0; top: 120px;
    text-align: center;
    font-family: "Barlow", sans-serif; font-weight: 600;
    font-size: 118px; line-height: 1; letter-spacing: 1px;
    color: var(--white);
  }
  .tagline {
    position: absolute; left: 0; right: 0; top: 300px;
    text-align: center;
    font-family: "Barlow", sans-serif; font-weight: 500; font-size: 30px;
    color: var(--white); letter-spacing: 0.5px;
  }
  /* Back side */
  .card--back { top: 577px; background: var(--white); }
  .dna-leaves {
    position: absolute; left: 22px; top: 26px; width: 270px; height: 411px;
  }
  .contact {
    position: absolute; left: 363px; top: 88px; width: 358px;
    font-family: "Barlow", sans-serif; color: var(--ink);
  }
  .contact__name { font-size: 28px; font-weight: 600; line-height: 1.05; }
  .contact__title { font-size: 18px; font-weight: 500; color: var(--green); line-height: 1.1; }
  .divider {
    border: none; border-top: 3px dotted var(--green);
    margin: 14px 0 15px;
  }
  .contact__list { list-style: none; font-size: 19px; line-height: 28px; }
  .contact__label { color: var(--green); font-weight: 600; margin-right: 4px; }
  .contact__address { font-size: 19px; line-height: 26px; font-style: normal; }
  .back-brand {
    position: absolute; left: 363px; bottom: 30px;
    display: flex; align-items: center; gap: 10px;
    font-family: "Barlow", sans-serif; font-weight: 600;
    font-size: 30px; line-height: 1; color: var(--green);
  }
  .back-brand__dot {
    width: 14px; height: 14px; border-radius: 50%; background: var(--green);
  }
</style>
</head>
<body>
<main class="canvas">
  <section class="card card--front" aria-label="Card front">
    <div class="brand-name">Plure</div>
    <p class="tagline">Smile from the Inside Out</p>
  </section>

  <section class="card card--back" aria-label="Card back">
    <svg class="dna-leaves" viewBox="0 0 270 411" role="img" aria-label="Illustration of a DNA helix sprouting two green leaves">
      <defs>
        <linearGradient id="leafTone" x1="0" y1="0" x2="0" y2="1">
          <stop offset="0" stop-color="#8cc63f"/>
          <stop offset="0.55" stop-color="#3fae49"/>
          <stop offset="1" stop-color="#c9cacc"/>
        </linearGradient>
      </defs>
      <rect x="0" y="0" width="270" height="411" rx="18" fill="url(#leafTone)" opacity="0.85"/>
    </svg>

    <div class="contact">
      <h1 class="contact__name">Dara Wendell</h1>
      <p class="contact__title">CEO</p>
      <hr class="divider">
      <ul class="contact__list">
        <li><span class="contact__label">Phone:</span>(555).210.3388</li>
        <li><span class="contact__label">Email:</span>hello@plurecare.com</li>
        <li><span class="contact__label">Web:</span>www.plurecare.com</li>
      </ul>
      <hr class="divider">
      <address class="contact__address">
        Your Address, 2nd Ste<br>
        Alder Falls, Texas 5521, USA
      </address>
    </div>

    <div class="back-brand"><span class="back-brand__dot"></span>Plure</div>
  </section>
</main>
</body>
</html>
```